The Aldermoor- outdoor banner

This should be a horizontal banner. It should have the logos attached incorporated and the following details
Coming Spring 2025: The Aldermoor - Exclusive Luxury Condos
Listed by Marisol Quennell | Fairlight Realty
Construction by Stonegate Build Group
Unveil the height of luxury living with The Aldermoor, a new condo building in East Boston, set for completion in Spring 2025. Experience a standard of elegance and sophistication like never before.
For more information and inquiries, please contact:
Marisol Quennell
Phone: (617) 430-9162
Email: marisol@fairlightprops.com
The banner should be very classy incorporting gold and navy very classic fonts. The Aldermoor should look very classy and exclusive. The stonegate build group logo should be smaller. It should not include their phone number and instagram handle only the name of the company. Herringbone pattern in the background would be great. This is going outside the building to advertise pre construction units

```html
<!DOCTYPE html>
<html lang="en">
<head>
<meta charset="utf-8">
<title>The Aldermoor – Outdoor Banner</title>
<link rel="stylesheet" href="https://fonts.googleapis.com/css2?family=Cinzel:wght@400;600&family=Jost:wght@500;600&family=Poppins:wght@400;500&family=Source+Serif+4:opsz,wght@8..60,600;8..60,700&family=Fira+Sans:wght@500;600&display=swap">
<style>
  :root {
    --navy: #1f2d4e;
    --gold: #e9b664;
    --cream: #f4f1ea;
    --white: #ffffff;
    --page: #e8ebf1;
  }
  * { margin: 0; padding: 0; box-sizing: border-box; }
  html, body { width: 946px; height: 1200px; overflow: hidden; background: var(--page); }
  .banner {
    position: absolute; left: 23px; top: 420px;
    width: 900px; height: 360px;
    background: var(--gold);
    box-shadow: 0 10px 28px rgba(20, 30, 60, .25);
    overflow: hidden;
  }
  .banner-shapes { position: absolute; inset: 0; }
  .banner > div, .banner > p { position: absolute; }

  /* left panel */
  .launch { left: 0; width: 231px; text-align: center; }
  .launch-coming { top: 20px; font: 600 27px/1 "Jost", sans-serif; color: var(--white); letter-spacing: -.5px; }
  .launch-season { top: 46px; font: 600 48px/1 "Jost", sans-serif; color: var(--white); letter-spacing: -1px; }
  .launch-year { top: 93px; font: 600 74px/1 "Jost", sans-serif; color: var(--gold); letter-spacing: -2px; }
  .launch-intro { top: 196px; left: 0; width: 231px; text-align: center; font: 400 9.2px/1.3 "Poppins", sans-serif; color: var(--white); }
  .launch-promise { top: 280px; left: 0; width: 231px; text-align: center; font: 600 11.2px/1.35 "Cinzel", serif; color: var(--gold); }

  /* title */
  .project-name { left: 256px; top: 12px; font: 700 86px/1 "Source Serif 4", serif; color: var(--navy); letter-spacing: -1.5px; white-space: nowrap; }
  .project-tagline { left: 270px; top: 97px; font: 600 24px/1 "Fira Sans", sans-serif; color: var(--cream); letter-spacing: 3px; white-space: nowrap; }

  /* builder */
  .builder-label { left: 257px; top: 158px; font: 500 10.5px/1 "Jost", sans-serif; color: var(--navy); }
  .builder-name { left: 245px; top: 200px; width: 128px; text-align: center; font: 600 11px/1.15 "Jost", sans-serif; color: var(--navy); letter-spacing: .5px; }
  .builder-name::before { content: ""; display: block; width: 14px; height: 14px; margin: 0 auto 6px; background: var(--navy); }

  .agent-photo {
    left: 379px; top: 161px; width: 80px; height: 80px; border-radius: 50%;
    border: 4px solid var(--gold);
    background: radial-gradient(circle at 50% 42%, #8a8a8a 0 30%, #3f4a66 60%, #3e5c94 100%);
  }

  /* listing */
  .listed-tag { left: 477px; top: 164px; width: 104px; height: 20px; background: var(--gold); font: 600 15px/20px "Fira Sans", sans-serif; color: var(--navy); letter-spacing: 1.2px; padding-left: 7px; }
  .agent-name { left: 477px; top: 192px; font: 600 24px/1 "Source Serif 4", serif; color: var(--white); white-space: nowrap; }
  .agent-firm { left: 477px; top: 221px; font: 400 12.5px/1 "Cinzel", serif; color: var(--gold); }

  .firm-mark { left: 690px; top: 196px; display: flex; align-items: center; gap: 9px; white-space: nowrap; }
  .firm-mark-dot { width: 16px; height: 16px; border-radius: 50%; background: var(--gold); }
  .firm-mark-name { font: 400 18px/1 "Cinzel", serif; color: var(--gold); }

  /* contact */
  .contact-lead { left: 256px; top: 268px; font: 500 13px/1 "Jost", sans-serif; color: var(--navy); white-space: nowrap; }
  .contact-name { left: 256px; top: 304px; font: 600 35px/1 "Source Serif 4", serif; color: var(--navy); letter-spacing: -.5px; white-space: nowrap; }
  .contact-lines { left: 571px; top: 304px; font: 400 15px/1.3 "Jost", sans-serif; color: var(--navy); white-space: nowrap; }
  .contact-lines strong { font-weight: 600; }
</style>
</head>
<body>
  <section class="banner" aria-label="The Aldermoor outdoor banner">
    <svg class="banner-shapes" width="900" height="360" viewBox="0 0 900 360" aria-hidden="true">
      <rect x="0" y="0" width="231" height="360" fill="var(--navy)"/>
      <polygon points="231,131 900,131 900,288 661,288 640,260 231,260" fill="var(--navy)"/>
      <polygon points="231,131 390,131 454,260 231,260" fill="var(--white)"/>
      <line x1="269" y1="126" x2="880" y2="126" stroke="var(--cream)" stroke-width="1"/>
      <line x1="477" y1="184" x2="650" y2="184" stroke="var(--gold)" stroke-width="1.5"/>
      <line x1="256" y1="288" x2="881" y2="288" stroke="var(--cream)" stroke-width="1"/>
      <line x1="551" y1="300" x2="551" y2="350" stroke="var(--cream)" stroke-width="1"/>
      <line x1="58" y1="181" x2="168" y2="181" stroke="var(--white)" stroke-width="1.5"/>
      <line x1="58" y1="261" x2="168" y2="261" stroke="var(--gold)" stroke-width="1.5"/>
    </svg>

    <div class="launch launch-coming">COMING</div>
    <div class="launch launch-season">SPRING</div>
    <div class="launch launch-year">2025</div>
    <p class="launch-intro">Unveil the height of luxury living<br>with The Aldermoor, a new condo<br>building in East Boston,<br>set for completion in Spring 2025.</p>
    <p class="launch-promise">EXPERIENCE A<br>STANDARD OF ELEGANCE<br>AND SOPHISTICATION LIKE<br>NEVER BEFORE.</p>

    <div class="project-name">The Aldermoor</div>
    <div class="project-tagline">EXCLUSIVE LUXURY CONDOS</div>

    <div class="builder-label">CONSTRUCTION BY</div>
    <div class="builder-name">STONEGATE BUILD GROUP</div>

    <div class="agent-photo" role="img" aria-label="Portrait of listing agent Marisol Quennell"></div>

    <div class="listed-tag">LISTED BY</div>
    <div class="agent-name">Marisol Quennell</div>
    <div class="agent-firm">FAIRLIGHT REALTY</div>

    <div class="firm-mark">
      <span class="firm-mark-dot"></span>
      <span class="firm-mark-name">FAIRLIGHT REALTY</span>
    </div>

    <div class="contact-lead">FOR MORE INFORMATION &amp; INQUIRIES, PLEASE CONTACT</div>
    <div class="contact-name">Marisol Quennell</div>
    <div class="contact-lines">
      <div><strong>PHONE:</strong> (617) 430-9162</div>
      <div><strong>EMAIL:</strong> marisol@fairlightprops.com</div>
    </div>
  </section>
</body>
</html>
```